Career Development Skills | Business Card & Logo Design

We are looking for a business card including logo design for a new Sydney based business called 'Bright Pathwork'.
We offer a range of services that focus on building the Employability or Employment skills for individuals focusing on job seekers and those interested in building skills required to develop their career. Employability skills are required not only to gain employment, but also to progress within an organisation so as to achieve one's potential.
Updates
Target Market(s)
Our client targets include corporates and govt agencies looking to build skills within their current employee base or assist staff in the transition between roles or workplaces.
Industry/Entity Type
Business
Look and feel
Each slider illustrates characteristics of the customer's brand and the style your logo design should communicate.

```html
<!DOCTYPE html>
<html lang="en">
<head>
<meta charset="utf-8">
<title>Bright Pathwork – Business Card</title>
<link rel="stylesheet" href="https://fonts.googleapis.com/css2?family=Cinzel:wght@700;900&family=Days+One&display=swap">
<style>
  :root {
    --backdrop: #1c1c1c;
    --card-dark: #0e0e0e;
    --card-mid: #2a2a2a;
    --card-light: #4a4a4a;
    --teal: #2bb5b8;
    --white: #f4f4f4;
    --rule: #bdbdbd;
    --ornament-light: #d8d8d8;
    --ornament-grey: #5a5a5a;
  }
  * { box-sizing: border-box; margin: 0; padding: 0; }
  html, body {
    width: 1200px;
    height: 1166px;
    overflow: hidden;
    background: var(--backdrop);
  }
  .canvas { position: relative; width: 1200px; height: 1166px; }

  .card {
    position: absolute;
    width: 736px;
    height: 450px;
    overflow: hidden;
    background:
      radial-gradient(ellipse 70% 60% at 85% 0%, rgba(255,255,255,0.22), rgba(255,255,255,0) 70%),
      linear-gradient(160deg, var(--card-mid) 0%, var(--card-dark) 55%, #161616 100%);
    box-shadow: 0 10px 30px rgba(0,0,0,0.6);
  }
  .card--front { left: 71px; top: 106px; }
  .card--back  { left: 410px; top: 601px; }

  .brand {
    position: absolute;
    left: 14px;
    top: 16px;
    display: flex;
    align-items: center;
    gap: 7px;
    font-family: "Days One", sans-serif;
    font-size: 13px;
    color: var(--teal);
    white-space: nowrap;
  }
  .brand__dot {
    width: 11px; height: 11px;
    border-radius: 50%;
    background: var(--teal);
  }

  .ornament { position: absolute; }
  .ornament--front-white {
    left: 180px; top: 0; width: 120px; height: 160px;
    background: radial-gradient(ellipse at 50% 40%, rgba(216,216,216,0.35), rgba(216,216,216,0) 70%);
  }
  .ornament--front-teal {
    left: 0; top: 220px; width: 200px; height: 230px;
    background: radial-gradient(ellipse at 30% 60%, rgba(43,181,184,0.45), rgba(43,181,184,0) 70%);
  }
  .ornament--front-grey {
    left: 0; top: 120px; width: 170px; height: 160px;
    background: radial-gradient(ellipse at 40% 50%, rgba(90,90,90,0.35), rgba(90,90,90,0) 70%);
  }
  .ornament--back-grey {
    left: 340px; top: 0; width: 396px; height: 450px;
    background: radial-gradient(ellipse at 70% 45%, rgba(150,150,150,0.3), rgba(90,90,90,0) 70%);
  }

  .rule { position: absolute; height: 2px; background: linear-gradient(90deg, rgba(189,189,189,0.2), var(--rule) 40%, var(--rule)); }
  .rule--thin { height: 1px; }

  .front__title {
    position: absolute;
    left: 297px;
    top: 188px;
    font-family: "Cinzel", serif;
    font-weight: 900;
    font-size: 34px;
    letter-spacing: 1px;
    color: var(--white);
    white-space: nowrap;
  }
  .front__role {
    position: absolute;
    left: 400px;
    top: 268px;
    font-family: "Days One", sans-serif;
    font-size: 15px;
    color: var(--teal);
    word-spacing: 6px;
    letter-spacing: 0.5px;
    white-space: nowrap;
  }
  .front__role span + span { margin-left: 26px; }

  .contact-panel {
    position: absolute;
    left: 0; top: 118px;
    width: 318px; height: 232px;
    background: linear-gradient(90deg, rgba(255,255,255,0.05), rgba(255,255,255,0.02));
  }
  .contact {
    position: absolute;
    left: 42px;
    top: 134px;
    font-family: "Days One", sans-serif;
    font-size: 15px;
    line-height: 21px;
    color: var(--white);
  }
  .contact__address { margin-bottom: 14px; }
  .contact__phones { color: var(--teal); margin-bottom: 10px; }
  .contact__label { display: inline-block; width: 70px; }
</style>
</head>
<body>
<main class="canvas">

  <section class="card card--front" aria-label="Business card front">
    <div class="ornament ornament--front-grey" role="img" aria-label="Faint grey floral swirl ornament"></div>
    <div class="ornament ornament--front-white" role="img" aria-label="White floral swirl ornament"></div>
    <div class="ornament ornament--front-teal" role="img" aria-label="Teal floral swirl ornament"></div>

    <div class="brand"><span class="brand__dot"></span>Bright Pathwork</div>

    <div class="rule" style="left:290px; top:162px; width:446px;"></div>
    <h1 class="front__title">Bright Pathwork</h1>
    <div class="rule rule--thin" style="left:290px; top:259px; width:446px;"></div>
    <p class="front__role"><span>DIRECTOR</span><span>DANIEL HART</span></p>
    <div class="rule rule--thin" style="left:382px; top:294px; width:270px;"></div>
  </section>

  <section class="card card--back" aria-label="Business card back">
    <div class="ornament ornament--back-grey" role="img" aria-label="Grey floral swirl ornament"></div>

    <div class="brand"><span class="brand__dot"></span>Bright Pathwork</div>

    <div class="contact-panel"></div>
    <div class="rule" style="left:0; top:117px; width:318px;"></div>

    <div class="contact">
      <p class="contact__address">
        Level 14<br>
        Harbour Point Tower 3<br>
        88 Kent Lane<br>
        Harbour Point, Sydney 2000
      </p>
      <p class="contact__phones">
        <span class="contact__label">Tel</span>(02) 5550 1234<br>
        <span class="contact__label">Fax</span>(02) 5550 1299
      </p>
      <p class="contact__web">
        brightpathwork.com.au<br>
        daniel@brightpathwork.com.au
      </p>
    </div>

    <div class="rule" style="left:0; top:351px; width:318px;"></div>
  </section>

</main>
</body>
</html>
```